Bramblewood Card Company Business Cards

We are a trading card store with Glimmorax, sports and other TCG cards, we need a business card design that encompasses a clean cut, modern style with a retro flare. website is bramblewoodcardco.com for reference. Can utilize a comic book era feel or a more modern outdoor feel to utilize the "Pacific Northwest" elements of tress, mountains, etc.

Industry/Entity Type

Trading cards and collectibles

Contact Information for Business Card

business name, email address, phone number, name, owner job title

Font styles to use
Sans Serif

```html
<!DOCTYPE html>
<html lang="en">
<head>
<meta charset="utf-8">
<title>Bramblewood Card Company – Business Cards</title>
<link href="https://fonts.googleapis.com/css2?family=Lato:wght@400;700&display=swap" rel="stylesheet">
<style>
  :root {
    --stage: #3a3a3a;
    --card: #000000;
    --slate: #6f6f6f;
    --slate-light: #8c8c8c;
    --snow: #e9e9e9;
    --cyan: #12b9e0;
    --white: #ffffff;
    --muted: #cfcfcf;
  }
  * { box-sizing: border-box; margin: 0; padding: 0; }
  html, body { width: 1200px; height: 689px; overflow: hidden; }
  body {
    background: var(--stage);
    font-family: "Lato", sans-serif;
    display: flex;
    align-items: center;
    justify-content: center;
    gap: 40px;
  }
  .card {
    position: relative;
    width: 540px;
    height: 310px;
    background: var(--card);
    border-radius: 18px;
    overflow: hidden;
  }
  .brand {
    display: flex;
    align-items: center;
    gap: 12px;
    color: var(--white);
    font-weight: 700;
    text-transform: uppercase;
    letter-spacing: 0.04em;
  }
  .brand-dot {
    flex: none;
    border-radius: 50%;
    background: var(--cyan);
  }

  /* Back */
  .card-back { display: flex; align-items: center; justify-content: center; }
  .card-back .brand { font-size: 24px; }
  .card-back .brand-dot { width: 22px; height: 22px; }

  /* Front */
  .card-front .brand {
    position: absolute;
    top: 36px;
    right: 28px;
    font-size: 13px;
    gap: 8px;
  }
  .card-front .brand-dot { width: 12px; height: 12px; }
  .scenery {
    position: absolute;
    inset: 0;
    background: linear-gradient(160deg, var(--slate-light) 0%, var(--slate) 45%, var(--slate) 70%, #7d7d7d 100%);
    clip-path: polygon(48% 100%, 66% 38%, 100% 38%, 100% 100%);
  }
  .scenery-glow {
    position: absolute;
    inset: 0;
    background: radial-gradient(ellipse 90px 70px at 78% 70%, rgba(233,233,233,0.55), rgba(233,233,233,0) 100%),
                radial-gradient(ellipse 60px 80px at 64% 78%, rgba(233,233,233,0.45), rgba(233,233,233,0) 100%);
    clip-path: polygon(48% 100%, 66% 38%, 100% 38%, 100% 100%);
  }
  .contact-block {
    position: absolute;
    left: 32px;
    top: 108px;
  }
  .person-name {
    color: var(--cyan);
    font-size: 28px;
    font-weight: 400;
    text-transform: uppercase;
    letter-spacing: 0.01em;
  }
  .person-title {
    color: var(--white);
    font-size: 15px;
    margin-top: 2px;
  }
  .contact-list { list-style: none; margin-top: 18px; }
  .contact-list li {
    display: flex;
    align-items: center;
    gap: 10px;
    color: var(--white);
    font-size: 14px;
    line-height: 1.7;
  }
  .contact-list svg { width: 14px; height: 14px; flex: none; fill: var(--muted); }
</style>
</head>
<body>
  <section class="card card-back" aria-label="Business card back">
    <div class="brand"><span class="brand-dot"></span>Bramblewood Card Company</div>
  </section>

  <section class="card card-front" aria-label="Business card front">
    <div class="scenery" role="img" aria-label="Grey and white Pacific Northwest mountain range illustration"></div>
    <div class="scenery-glow" aria-hidden="true"></div>
    <div class="brand"><span class="brand-dot"></span>Bramblewood Card Company</div>
    <div class="contact-block">
      <h1 class="person-name">Dorian Hale</h1>
      <p class="person-title">Managing Director</p>
      <ul class="contact-list">
        <li>
          <svg viewBox="0 0 16 16" aria-hidden="true"><path d="M3.5 1.5l2.5 0 1 3.5-1.6 1.2a8 8 0 0 0 4.4 4.4L11 9l3.5 1v2.5c0 1-1 2-2 2A11 11 0 0 1 1.5 3.5c0-1 1-2 2-2z"/></svg>
          044-987 654 321
        </li>
        <li>
          <svg viewBox="0 0 16 16" aria-hidden="true"><path d="M1 3h14v10H1z M2 4v.4l6 4.2 6-4.2V4z" fill-rule="evenodd"/></svg>
          info@bramblewoodmail.com
        </li>
        <li>
          <svg viewBox="0 0 16 16" aria-hidden="true"><circle cx="8" cy="8" r="7" fill="none" stroke="#cfcfcf" stroke-width="1.5"/><path d="M1 8h14M8 1c-3 3.5-3 10.5 0 14M8 1c3 3.5 3 10.5 0 14" fill="none" stroke="#cfcfcf" stroke-width="1.2"/></svg>
          www.bramblewoodcardco.com
        </li>
      </ul>
    </div>
  </section>
</body>
</html>
```